Packaging design for a reclosable bag for our product

We have a logo, and we need to put it on packaging for our product and while we want the look to be simple, we want it to follow good design principles and also contain spaces for other product descriptions.

There will be 5 sizes at launch so I'd like 5 variations, one for each size.

I've included a few mockups of the type of bag that I made but they are all just rough ideas that I had.

I want the brand to look scientific and methodical and even a bit quirky, as in "wow this is a serious product but also a bit unusual."

```html
<!DOCTYPE html>
<html lang="en">
<head>
<meta charset="UTF-8">
<title>Veyra Bias Lighting Pouch</title>
<link href="https://fonts.googleapis.com/css2?family=Open+Sans:wght@300;400;700&display=swap" rel="stylesheet">
<style>
  :root{
    --page:#ffffff;
    --pouch-dark:#0b0b0b;
    --pouch-light:#f3f3f3;
    --brand-on-dark:#808080;
    --brand-on-light:#767676;
    --ink-on-dark:#e6e6e6;
    --ink-on-light:#111111;
    --caption:#8a8a8a;
  }
  *{margin:0;padding:0;box-sizing:border-box}
  html,body{width:1200px;height:1040px;overflow:hidden;background:var(--page)}
  body{position:relative;font-family:"Open Sans",sans-serif}
  .pouch{
    position:absolute;top:74px;width:458px;height:652px;
    border-radius:22px 22px 2px 2px;
    box-shadow:0 14px 16px -10px rgba(0,0,0,.22);
  }
  .pouch--dark{left:148px;background:var(--pouch-dark);color:var(--ink-on-dark)}
  .pouch--light{left:646px;background:var(--pouch-light);color:var(--ink-on-light)}
  .pouch__zip{position:absolute;left:28px;right:28px;top:84px;height:1px;background:rgba(0,0,0,.06)}
  .pouch--dark .pouch__zip{background:rgba(255,255,255,.04)}
  .brand{
    position:absolute;left:33px;top:196px;
    font-size:122px;font-weight:700;line-height:1;letter-spacing:-2px;
  }
  .pouch--dark .brand{color:var(--brand-on-dark)}
  .pouch--light .brand{color:var(--brand-on-light)}
  .size{position:absolute;left:188px;top:542px;width:60px;text-align:center}
  .size__value{display:block;font-size:66px;font-weight:700;line-height:66px}
  .size__unit{display:block;font-size:19px;font-weight:300;line-height:22px}
  .specs{
    position:absolute;left:267px;top:545px;list-style:none;
    font-size:16px;font-weight:300;line-height:20px;white-space:nowrap;
  }
  .caption{
    position:absolute;left:0;right:0;top:918px;text-align:center;
    font-size:15px;font-weight:400;color:var(--caption);
  }
</style>
</head>
<body>
  <section class="pouch pouch--dark">
    <div class="pouch__zip"></div>
    <div class="brand">VEYRA</div>
    <div class="size"><span class="size__value">5</span><span class="size__unit">meters</span></div>
    <ul class="specs">
      <li>Extra Large</li>
      <li>Bias Lighting</li>
      <li>Simulated D65 CRI 90+</li>
      <li>6500K White</li>
    </ul>
  </section>

  <section class="pouch pouch--light">
    <div class="pouch__zip"></div>
    <div class="brand">VEYRA</div>
    <div class="size"><span class="size__value">5</span><span class="size__unit">meters</span></div>
    <ul class="specs">
      <li>Extra Large</li>
      <li>Bias Lighting</li>
      <li>Simulated D65 CRI 90+</li>
      <li>6500K White</li>
    </ul>
  </section>

  <p class="caption">revised with 18% gray</p>
</body>
</html>
```